Maris Dovey Studio Business Cards

Hi - using the information and logo provided I require a two sided business card designed with the following information. The business card is a 'mini card' 3.5" x 1.25".

Front of card should be the logo attached but inverted (so the background is the peach colour and the logo white).

Back should have these details. If we can't fit the Pictogrum and Friendwall part can we just put the little logos.

Tessa Varnold

Art and Design Consultant
Dealer - Curator - Events - Styling - Creative Sourcing

P: 0438 217 604
E: tessa@marisdoveystudio.example
W: www.marisdoveystudio.example
I (pictogram image please): marisdoveystudio F (Friendwall image please): MarisDoveyAdviser

Target Market(s)

Galleries, artists, art buyers, interior design clients, event managers, creative types

Industry/Entity Type

Business

```html
<!DOCTYPE html>
<html lang="en">
<head>
<meta charset="utf-8">
<title>Maris Dovey Studio – Mini Business Card</title>
<link rel="stylesheet" href="https://fonts.googleapis.com/css2?family=Arimo:wght@400&family=Cormorant+Garamond:wght@500&display=swap">
<style>
  :root {
    --backdrop: #8d8d8f;
    --peach: #f5b799;
    --peach-text: #f0a983;
    --card-white: #fbfbfa;
    --ink: #555557;
    --ink-soft: #6a6a6c;
    --rule: #e1d9d4;
    --on-peach: #ffffff;
  }
  * { box-sizing: border-box; margin: 0; padding: 0; }
  html, body {
    width: 1200px;
    height: 910px;
    overflow: hidden;
    background: var(--backdrop);
  }
  .canvas {
    width: 1200px;
    height: 910px;
    display: flex;
    flex-direction: column;
    align-items: center;
    justify-content: center;
    gap: 60px;
  }
  .card {
    width: 1000px;
    height: 357px;
    position: relative;
    box-shadow: 0 6px 18px rgba(0, 0, 0, 0.18);
  }

  /* Front */
  .card-front {
    background: var(--peach);
    display: flex;
    align-items: center;
    justify-content: center;
    gap: 20px;
  }
  .brand-circle {
    width: 44px;
    height: 44px;
    display: block;
    flex: none;
  }
  .brand-name {
    font-family: "Arimo", Arial, sans-serif;
    font-weight: 400;
    font-size: 34px;
    line-height: 1;
    color: var(--on-peach);
  }

  /* Back */
  .card-back {
    background: var(--card-white);
    text-align: center;
    font-family: "Arimo", Arial, sans-serif;
    color: var(--ink);
    padding-top: 40px;
  }
  .person-name {
    font-family: "Cormorant Garamond", Georgia, serif;
    font-weight: 500;
    font-size: 50px;
    line-height: 1;
    color: var(--peach-text);
    letter-spacing: 0.01em;
  }
  .role {
    margin-top: 16px;
    font-size: 22px;
  }
  .services {
    margin-top: 8px;
    font-size: 22px;
  }
  .divider {
    width: 820px;
    height: 1px;
    margin: 20px auto 0;
    background: var(--rule);
  }
  .social {
    margin-top: 18px;
    display: flex;
    justify-content: center;
    gap: 34px;
    font-size: 21px;
    color: var(--ink-soft);
  }
  .social-item {
    display: flex;
    align-items: center;
    gap: 10px;
  }
  .social-mark {
    width: 20px;
    height: 20px;
    background: var(--peach-text);
    border-radius: 3px;
  }
  .contact {
    margin-top: 30px;
    font-size: 23px;
    color: var(--ink-soft);
  }
  .contact .sep { margin: 0 6px; }
</style>
</head>
<body>
<main class="canvas">
  <section class="card card-front" aria-label="Card front">
    <svg class="brand-circle" viewBox="0 0 44 44" aria-hidden="true">
      <circle cx="22" cy="22" r="20" fill="none" stroke="#ffffff" stroke-width="2"/>
    </svg>
    <p class="brand-name">Maris Dovey Studio</p>
  </section>

  <section class="card card-back" aria-label="Card back">
    <h1 class="person-name">Tessa Varnold</h1>
    <p class="role">Art and Design Consultant</p>
    <p class="services">Dealer - Curator - Events - Styling - Creative Sourcing</p>
    <div class="divider"></div>
    <div class="social">
      <span class="social-item"><span class="social-mark" aria-label="Pictogrum"></span>marisdoveystudio</span>
      <span class="social-item"><span class="social-mark" aria-label="Friendwall"></span>MarisDoveyAdviser</span>
    </div>
    <p class="contact">0438 217 604<span class="sep">|</span>tessa@marisdoveystudio.example<span class="sep">|</span>www.marisdoveystudio.example</p>
  </section>
</main>
</body>
</html>
```